Brightway Haul & Upkeep Services, are a company that offers a 'one stop shop' pre-move clean up a

I have already selected a logo which I would like on the front of the business cards along with phone numbers, web address and email which are:
0487650392
www.brightwayhaul.com.au
brightwayhaulandupkeep@mailbox.example

On the back of the card I would like to list some of the types of service we offer (clean - move - repairs/maintenance) which are:
CLEAN - windows, gutters, solar panels, driveways/paths, carpets.
MOVE - Small/medium size house/office moves, large item pick-up & delivery, yard clean-up and removal.
General maintenance and repairs.

I would like the blue logo on a gray background.

Thanks

```html
<!DOCTYPE html>
<html lang="en">
<head>
<meta charset="utf-8">
<title>Brightway Haul &amp; Upkeep Services – Business Card</title>
<link rel="stylesheet" href="https://fonts.googleapis.com/css2?family=Source+Sans+3:wght@400;600;700&family=Josefin+Sans:wght@400&display=swap">
<style>
  :root {
    --page-bg: #e9e6e2;
    --card-grey: #c9cacc;
    --brand-blue: #2f76c9;
    --band-dark: #3b3d40;
    --ink: #2a2b2d;
    --divider: #f2f2f2;
  }
  * { margin: 0; padding: 0; box-sizing: border-box; }
  html, body {
    width: 1200px; height: 788px; overflow: hidden;
    background: var(--page-bg);
  }
  .stage {
    position: relative; width: 1200px; height: 788px;
    display: flex; align-items: center; justify-content: center; gap: 40px;
  }
  .card {
    position: relative; width: 540px; height: 309px;
    background: var(--card-grey);
    box-shadow: 0 6px 18px rgba(0,0,0,.25);
    overflow: hidden;
  }

  /* Front card */
  .front-brand {
    position: absolute; left: 30px; top: 104px; width: 200px;
    display: flex; align-items: flex-start; gap: 10px;
  }
  .brand-square {
    flex: none; width: 16px; height: 16px; margin-top: 5px;
    background: var(--brand-blue);
  }
  .brand-name {
    font-family: "Source Sans 3", sans-serif; font-weight: 700;
    color: var(--brand-blue); text-transform: uppercase;
    font-size: 20px; line-height: 1.1;
  }
  .front-divider {
    position: absolute; left: 248px; top: 54px; width: 2px; height: 118px;
    background: var(--divider);
  }
  .contact-list {
    position: absolute; left: 264px; right: 24px; top: 58px; list-style: none;
    font-family: "Josefin Sans", sans-serif; color: var(--ink);
  }
  .contact-item {
    display: flex; align-items: center; gap: 8px;
    margin-bottom: 14px; font-size: 11px; white-space: nowrap;
  }
  .contact-item.phone { font-size: 16px; }
  .contact-icon { width: 11px; height: 11px; flex: none; }
  .front-band-line {
    position: absolute; left: 0; right: 0; bottom: 40px; height: 2px;
    background: var(--band-dark);
  }
  .front-band {
    position: absolute; left: 0; right: 0; bottom: 0; height: 36px;
    background: var(--brand-blue);
  }

  /* Back card */
  .back-brand {
    position: absolute; left: 44px; top: 40px; right: 36px;
    display: flex; align-items: flex-start; gap: 14px;
  }
  .back-brand .brand-square { width: 26px; height: 26px; margin-top: 10px; }
  .back-brand .brand-name { font-size: 40px; line-height: 1.05; }
  .services-title {
    position: absolute; left: 0; right: 0; top: 178px; text-align: center;
    font-family: "Source Sans 3", sans-serif; font-weight: 600;
    color: var(--brand-blue); font-size: 20px; letter-spacing: 6px;
  }
  .services-list {
    position: absolute; left: 0; right: 0; top: 214px; text-align: center;
    font-family: "Source Sans 3", sans-serif; font-weight: 600;
    color: var(--ink); font-size: 18px; line-height: 1.35; list-style: none;
  }
  .services-row span + span { margin-left: 24px; }
</style>
</head>
<body>
<main class="stage">
  <section class="card card-front" aria-label="Card front">
    <div class="front-brand">
      <span class="brand-square" aria-hidden="true"></span>
      <span class="brand-name">Brightway Haul &amp; Upkeep Services</span>
    </div>
    <div class="front-divider"></div>
    <ul class="contact-list">
      <li class="contact-item phone">
        <svg class="contact-icon" viewBox="0 0 12 12" aria-hidden="true"><circle cx="6" cy="6" r="5.5" fill="none" stroke="#2a2b2d" stroke-width="1"/><path d="M4 3.2l1 .2.4 1.4-.7.6a4 4 0 0 0 1.9 1.9l.6-.7 1.4.4.2 1a1 1 0 0 1-1 .8A4.8 4.8 0 0 1 3.2 4.2a1 1 0 0 1 .8-1z" fill="#2a2b2d"/></svg>
        0487650392
      </li>
      <li class="contact-item">
        <svg class="contact-icon" viewBox="0 0 12 12" aria-hidden="true"><rect x="1" y="3" width="10" height="7" fill="none" stroke="#2a2b2d"/><path d="M1 3l5 4 5-4" fill="none" stroke="#2a2b2d"/></svg>
        brightwayhaulandupkeep@mailbox.example
      </li>
      <li class="contact-item">
        <svg class="contact-icon" viewBox="0 0 12 12" aria-hidden="true"><circle cx="6" cy="6" r="5" fill="none" stroke="#2a2b2d"/><ellipse cx="6" cy="6" rx="2.2" ry="5" fill="none" stroke="#2a2b2d"/><path d="M1 6h10" stroke="#2a2b2d"/></svg>
        www.brightwayhaul.com.au
      </li>
    </ul>
    <div class="front-band-line"></div>
    <div class="front-band"></div>
  </section>

  <section class="card card-back" aria-label="Card back">
    <div class="back-brand">
      <span class="brand-square" aria-hidden="true"></span>
      <span class="brand-name">Brightway Haul &amp; Upkeep Services</span>
    </div>
    <h2 class="services-title">Services we offer</h2>
    <ul class="services-list">
      <li class="services-row"><span>• Clean</span><span>• Move</span></li>
      <li>• General maintenance and repairs.</li>
    </ul>
  </section>
</main>
</body>
</html>
```